Marwick Law Letterhead

We need a new letterhead design for a Law Firm. The address for the law firm is 1475 Calloway Street, Suite 210, Houston, Texas 77041. Phone Number: 832-361-9027; Fax Number: 832-614-7359. The logo is uploaded to the project.

```html
<!DOCTYPE html>
<html lang="en">
<head>
<meta charset="utf-8">
<title>Marwick Law Letterhead</title>
<link href="https://fonts.googleapis.com/css2?family=Montserrat:wght@400;500;600&display=swap" rel="stylesheet">
<style>
  :root {
    --backdrop: #e8e8e8;
    --paper: #ffffff;
    --navy: #1a2f5a;
    --red: #d71a28;
    --red-deep: #6b0a14;
    --ink: #2a2a2a;
    --ink-dark: #111111;
  }
  * { margin: 0; padding: 0; box-sizing: border-box; }
  html, body {
    width: 1154px; height: 1200px; overflow: hidden;
    background: var(--backdrop);
    font-family: "Montserrat", sans-serif;
  }
  .letterhead {
    position: absolute; left: 154px; top: 9px;
    width: 846px; height: 1182px;
    background: var(--paper);
    color: var(--ink);
  }
  .brand {
    position: absolute; left: 33px; top: 68px;
    display: flex; align-items: center; gap: 12px;
  }
  .brand-mark {
    width: 30px; height: 30px; border-radius: 50%;
    background: var(--navy);
  }
  .brand-name {
    font-size: 30px; font-weight: 600; color: var(--navy);
    letter-spacing: 0.5px;
  }
  .contact {
    position: absolute; left: 640px; top: 52px;
    font-size: 14px; line-height: 18px; color: var(--ink-dark);
  }
  .contact-line { display: flex; align-items: center; gap: 8px; margin-top: 4px; }
  .contact-address { margin-bottom: 6px; }
  .contact-line svg { width: 13px; height: 13px; fill: var(--red); }
  .header-rule {
    position: absolute; left: 30px; top: 195px;
    width: 784px; height: 4px; background: var(--red);
  }
  .recipient {
    position: absolute; left: 31px; top: 283px;
    font-size: 14px; line-height: 21px; color: var(--ink-dark);
  }
  .letter-body {
    position: absolute; left: 33px; top: 371px; width: 784px;
    font-size: 13.6px; line-height: 21px; text-align: justify;
    color: var(--ink);
  }
  .letter-body p + p { margin-top: 21px; }
  .sign-off {
    position: absolute; left: 31px; top: 964px;
    font-size: 17px; color: var(--ink-dark);
  }
  .signature {
    position: absolute; left: 29px; top: 1000px;
    width: 96px; height: 24px;
  }
  .footer-band {
    position: absolute; left: 0; bottom: 0;
    width: 846px; height: 54px; display: block;
  }
</style>
</head>
<body>
  <main class="letterhead">
    <header>
      <div class="brand">
        <span class="brand-mark"></span>
        <span class="brand-name">Marwick Law</span>
      </div>
      <address class="contact" style="font-style:normal">
        <div class="contact-address">1475 Calloway Street,<br>Suite 210, Houston,<br>Texas 77041</div>
        <div class="contact-line">
          <svg viewBox="0 0 24 24" aria-hidden="true"><path d="M6.6 10.8a15.1 15.1 0 0 0 6.6 6.6l2.2-2.2a1 1 0 0 1 1-.25 11.4 11.4 0 0 0 3.6.57 1 1 0 0 1 1 1V20a1 1 0 0 1-1 1A17 17 0 0 1 3 4a1 1 0 0 1 1-1h3.5a1 1 0 0 1 1 1c0 1.25.2 2.45.57 3.6a1 1 0 0 1-.25 1z"/></svg>
          <span>832-361-9027</span>
        </div>
        <div class="contact-line">
          <svg viewBox="0 0 24 24" aria-hidden="true"><path d="M7 2h10v5H7zM4 8h16a2 2 0 0 1 2 2v7h-4v5H6v-5H2v-7a2 2 0 0 1 2-2zm4 8v4h8v-4z"/></svg>
          <span>832-614-7359</span>
        </div>
      </address>
      <div class="header-rule"></div>
    </header>

    <section class="recipient">
      <div>Mr/s</div>
      <div>First Name and Last Name</div>
      <div>Company Name</div>
      <div>Address</div>
    </section>

    <section class="letter-body">
      <p>Lorem ipsum dolor sit amet,consectetur adipiscing sed do eiusmod tempor incididunt laboreet dolore magna aliqua.Ut enim ad minim.veniam, quis nostrud exercitation ullamco laboris nisi ut aliquip exea commodo consequat.Lorem ipsum dolor sit amet,consectetur adipiscing sed do eiusmod tempor incididunt.labore et dolore magna aliqua. Ut enim</p>
      <p>Lorem ipsum dolor sit amet, consectetur adipiscing sed do eiusmod tempor incididunt labore et dolore magna aliqua. Ut enim ad minim veniam, quis nostrud exercitation ullamco laboris nisi ut aliquip exea commodo consequat.Duis aute irure dolor in reprehenderit in voluptate velit esse cillum irure dolor in reprehenderit in voluptate velit esse irure</p>
      <p>Lorem ipsum dolor sit amet, consectetur adipiscing sed do eiusmod tempor incididunt labore et dolore magna aliqua. consequat. Duis aute irure dolor in.reprehenderit in voluptate velit esse cillum dolore eu fugiat nulla pariatur. Excepteur sint occaecat cupidatat non proident, sunt in culpa qui officia deserunt mollit,</p>
      <p>Lorem ipsum dolor sit amet, consectetur adipiscing sed do eiusmod tempor incididunt labore et dolore magna aliqua. Ut enim Lorem ipsum dolor sit amet, consectetur adipiscing sed do eiusmod tempor incididunt labore et dolore magna aliqua. Ut enim Lorem ipsum aliqua.ipsum</p>
      <p>Lorem ipsum dolor sit amet, consectetur adipiscing sed do eiusmod tempor incididunt labore et dolore magna aliqua. Ut enim ad minim veniam, quis nostrud exercitation ullamco laboris nisi ut aliquip exea commodo consequat.Duis aute irure dolor in reprehenderit in voluptate velit esse cillum irure dolor in reprehenderit in voluptate velit esse irure</p>
      <p>Lorem ipsum dolor sit amet, consectetur adipiscing sed do eiusmod tempor incididunt labore et dolore magna aliqua. Ut enim ad minim veniam, quis nostrud exercitation ullamco laboris nisi ut aliquip exea commodo consequat.Duis aute irure dolor in reprehenderit in voluptate velit esse cillum irure dolor in reprehenderit in voluptate velit esse irure</p>
    </section>

    <div class="sign-off">Regards</div>
    <svg class="signature" viewBox="0 0 96 24" role="img" aria-label="Handwritten signature of the sender">
      <rect x="0" y="0" width="96" height="24" rx="3" fill="#111111" opacity="0.12"/>
    </svg>

    <svg class="footer-band" viewBox="0 0 846 54" aria-hidden="true">
      <defs>
        <linearGradient id="band-red" x1="0" y1="0" x2="1" y2="0">
          <stop offset="0" stop-color="#d71a28"/>
          <stop offset="0.6" stop-color="#d71a28"/>
          <stop offset="1" stop-color="#6b0a14"/>
        </linearGradient>
      </defs>
      <polygon points="0,0 450,0 421,54 0,54" fill="#1a2f5a"/>
      <polygon points="460,0 846,0 846,54 431,54" fill="url(#band-red)"/>
    </svg>
  </main>
</body>
</html>
```